Automotive eCommerce Business looking for a business card design

Looking for a clean and simple business card design. Our company name is "Brindle Auto" and we are a company specializing in the ecommerce sales of automotive parts, specifically for pick up trucks and large SUVs. Our company colours are red, black, and white.

Feel free to use the logo provided or create a new logo that you seem fit. Looking forward to your creative ideas!

Industry/Entity Type

Automotive

Contact Information for Business Card

We were thinking of a possibly two-sided design featuring just the logo and company name on one side, and personal information on the other side. Single sided designs will be considered as well.

Font styles to use
Serif
Sans Serif
Decorative

Colors
ec1f27
ffffff
000000

Requirements
Must have
• Space for employee's name, title, phone number and email address, along with the company address and website somewhere.

```html
<!DOCTYPE html>
<html lang="en">
<head>
<meta charset="utf-8">
<title>Brindle Auto – Business Card</title>
<link rel="stylesheet" href="https://fonts.googleapis.com/css2?family=Cinzel:wght@500&family=Roboto:wght@400;500&display=swap">
<style>
  :root {
    --brand-red: #a01c22;
    --ink: #3f3f3f;
    --ink-soft: #555555;
    --rule: #8a8a8a;
    --card-white: #f4f4f4;
    --band-grey: #55585b;
    --page: #e6e3df;
    --white: #ffffff;
  }
  * { margin: 0; padding: 0; box-sizing: border-box; }
  html, body { width: 1200px; height: 960px; overflow: hidden; }
  body {
    position: relative;
    background: var(--page);
    font-family: "Roboto", Arial, sans-serif;
  }
  .card {
    position: absolute;
    width: 600px;
    height: 342px;
    border-radius: 22px;
    overflow: hidden;
  }
  /* Front side */
  .card-front {
    left: 320px; top: 108px;
    background: var(--brand-red);
    color: var(--white);
  }
  .front-name {
    position: absolute;
    left: 0; right: 0; top: 140px;
    text-align: center;
    font-family: "Cinzel", Georgia, serif;
    font-weight: 500;
    font-size: 44px;
    letter-spacing: 2px;
  }
  .front-web {
    position: absolute;
    left: 0; right: 0; top: 296px;
    text-align: center;
    font-size: 15px;
    letter-spacing: 5px;
  }
  /* Back side */
  .card-back {
    left: 320px; top: 493px;
    background: var(--card-white);
    color: var(--ink);
  }
  .brand-dot {
    position: absolute;
    left: 446px; top: 48px;
    width: 58px; height: 58px;
    border-radius: 50%;
    background: var(--brand-red);
  }
  .brand-name {
    position: absolute;
    right: 36px; top: 154px;
    font-family: "Cinzel", Georgia, serif;
    font-weight: 500;
    font-size: 19px;
    color: var(--ink-soft);
    letter-spacing: 0.5px;
  }
  .person-name {
    position: absolute;
    left: 33px; top: 178px;
    font-size: 22px;
    font-weight: 500;
    color: var(--brand-red);
  }
  .person-title {
    position: absolute;
    left: 33px; top: 206px;
    font-size: 14px;
    font-weight: 500;
    color: var(--ink);
  }
  .divider {
    position: absolute;
    left: 33px; right: 38px; top: 230px;
    height: 1px;
    background: var(--rule);
  }
  .contact-list {
    position: absolute;
    left: 33px; top: 239px;
    list-style: none;
    font-size: 14px;
    line-height: 19px;
  }
  .contact-list li { display: flex; align-items: center; gap: 8px; }
  .contact-list svg { width: 14px; height: 14px; fill: var(--brand-red); }
  .address {
    position: absolute;
    right: 38px; top: 249px;
    text-align: right;
    font-size: 14px;
    line-height: 19px;
  }
  .base-band {
    position: absolute;
    left: 0; bottom: 0;
    width: 100%; height: 14px;
  }
</style>
</head>
<body>
  <section class="card card-front">
    <div class="front-name">BRINDLE AUTO</div>
    <div class="front-web">www.brindleauto.com</div>
  </section>

  <section class="card card-back">
    <div class="brand-dot"></div>
    <div class="brand-name">Brindle Auto Ltd.</div>

    <div class="person-name">EVAN MARSH</div>
    <div class="person-title">CEO/FOUNDER</div>
    <div class="divider"></div>

    <ul class="contact-list">
      <li><svg viewBox="0 0 24 24" aria-hidden="true"><path d="M6.6 10.8a15.1 15.1 0 0 0 6.6 6.6l2.2-2.2c.3-.3.7-.4 1-.2 1.1.4 2.3.6 3.6.6.6 0 1 .4 1 1V20c0 .6-.4 1-1 1A17 17 0 0 1 3 4c0-.6.4-1 1-1h3.5c.6 0 1 .4 1 1 0 1.3.2 2.5.6 3.6.1.3 0 .7-.2 1z"/></svg>555 214 7730</li>
      <li><svg viewBox="0 0 24 24" aria-hidden="true"><path d="M7 1h10a2 2 0 0 1 2 2v18a2 2 0 0 1-2 2H7a2 2 0 0 1-2-2V3a2 2 0 0 1 2-2zm0 3v14h10V4z"/></svg>555 309 4182</li>
      <li><svg viewBox="0 0 24 24" aria-hidden="true"><path d="M6 2h10l3 3v5H6zM3 11h18a1 1 0 0 1 1 1v9a1 1 0 0 1-1 1H3a1 1 0 0 1-1-1v-9a1 1 0 0 1 1-1zm3 3v2h12v-2z"/></svg>555 762 0915</li>
      <li><svg viewBox="0 0 24 24" aria-hidden="true"><path d="M2 5h20v2l-10 6L2 7zm0 4.3 10 6 10-6V19H2z"/></svg>evan@brindleauto.com</li>
    </ul>

    <address class="address" style="font-style:normal">
      2140 Cedar Ridge Road<br>
      Fairbanks, Alaska 99701<br>
      www.brindleauto.com
    </address>

    <svg class="base-band" viewBox="0 0 600 14" preserveAspectRatio="none" aria-hidden="true">
      <polygon points="0,0 392,0 388,14 0,14" fill="var(--brand-red)"/>
      <polygon points="396,0 600,0 600,14 392,14" fill="var(--band-grey)"/>
    </svg>
  </section>
</body>
</html>
```